Wine Label design for a Grapefruit flavored wine

We need a wine label for a wine that is flavored with grapefruit flavors and slightly sparkling.It should be eye catching and fun. It will be sold in the United States market. We like the idea of using a pink flamingo and/or grapefruits. Just one flamingo please if you use a flamingo. There is no size restriction on the label size. Something super eye catching and super fun.

Attached are some images we like, these are for your reference only, they are not good quality for print. You can choose to do something with a flamingo or with grapefruits or both together. Something bold is what we are looking for too. You can even use a clear label. We really don't mind seeing some fun and bold colors.

The name of the wine is: Vela di Corallo
In small letters please put this sentence:

Grape wine with natural grapefruit, peach flavor, carbonation added
It is a white wine in a clear Bordeaux style bottle with a screw cap.

```html
<!DOCTYPE html>
<html lang="en">
<head>
<meta charset="utf-8">
<title>Vela di Corallo – Wine Label</title>
<link rel="stylesheet" href="https://fonts.googleapis.com/css2?family=Cormorant+Garamond:wght@500;600&display=swap">
<style>
  :root {
    --backdrop: #16202f;
    --label-paper: #f4f4f5;
    --label-edge: #a3a8b0;
    --cutout-ring: #6e737b;
    --ink: #2a2d33;
    --coral: #d7637d;
    --fruit-pink: #f2a3b8;
    --fruit-rind: #f1b55a;
  }
  html, body {
    margin: 0;
    padding: 0;
    width: 1200px;
    height: 1200px;
    overflow: hidden;
    background: var(--backdrop);
  }
  .canvas {
    position: relative;
    width: 1200px;
    height: 1200px;
    display: flex;
    align-items: center;
    justify-content: center;
  }
  .wine-label {
    width: 640px;
    height: 860px;
    display: block;
  }
  .label-paper { fill: var(--label-paper); stroke: var(--label-edge); stroke-width: 7; }
  .label-cutout { fill: var(--backdrop); stroke: var(--cutout-ring); stroke-width: 9; }
  .fruit-rind { fill: var(--fruit-rind); }
  .fruit-slice { fill: url(#fruitTone); }
  .wine-name {
    font-family: "Cormorant Garamond", serif;
    font-weight: 600;
    font-size: 50px;
    letter-spacing: 0.06em;
    fill: var(--ink);
  }
  .wine-flavor {
    font-family: "Cormorant Garamond", serif;
    font-weight: 600;
    font-size: 26px;
    letter-spacing: 0.2em;
    fill: var(--coral);
  }
  .wine-origin {
    font-family: "Cormorant Garamond", serif;
    font-weight: 600;
    font-size: 24px;
    letter-spacing: 0.3em;
    fill: var(--ink);
  }
</style>
</head>
<body>
<main class="canvas">
  <svg class="wine-label" viewBox="0 0 640 860" xmlns="http://www.w3.org/2000/svg">
    <defs>
      <radialGradient id="fruitTone" cx="50%" cy="50%" r="50%">
        <stop offset="0%" stop-color="#fbe3ea"/>
        <stop offset="100%" stop-color="var(--fruit-pink)"/>
      </radialGradient>
    </defs>

    <path class="label-paper"
          d="M 300 40
             L 580 40
             L 580 780
             Q 580 820 540 820
             L 100 820
             Q 60 820 60 780
             L 60 290
             A 250 250 0 0 1 300 40 Z"/>

    <circle class="label-cutout" cx="430" cy="250" r="205"/>

    <g role="img" aria-label="Illustration of a pink grapefruit slice">
      <circle class="fruit-rind" cx="455" cy="225" r="180"/>
      <circle class="fruit-slice" cx="455" cy="225" r="166"/>
    </g>

    <text class="wine-name" x="320" y="620" text-anchor="middle">VELA DI CORALLO</text>
    <text class="wine-flavor" x="320" y="660" text-anchor="middle">GRAPEFRUIT FLAVORS</text>
    <text class="wine-origin" x="320" y="770" text-anchor="middle">USA</text>
  </svg>
</main>
</body>
</html>
```